International Clinical Software Company needs a new business card design

We are looking for a new business card design for our company that has recently expanded into the UK market, making us a multinational company.
After having rebranded our website and produced a new style guide, we are looking for a business card that is creative and attention grabbing, while being consistent with the style and colour scheme used on the new website, www.plumvora.example
We produce care management technology for the aged care market, but the main aspect we aim to communicate is the human element of our software, and the way it assists in providing better care for aged people, and stronger relationships between aged people and the staff that care for them.
Our current business card is a dark green with gold text, which makes the text quite difficult to read, not very aesthetically appealing and the colour scheme looks quite dated.
We would like something fresh and modern, that can still be colourful but doesn't use large blocks of dark colour, and uses the colours within our logo.
Something tying in with the leaves that are used in our logo could work quite nicely, along with the Autumn/Fall colours of soft greens, yellows and reds (also in our existing logo). However also happy to look at fresh, completely out of the box ideas we may not have yet considered.
Target Market(s)
The people that receive this business card work in the aged card or health industry and are either corporate/management level staff or clinical (Registered Nurses, care workers etc.)
Industry/Entity Type
Health Product
Contact Information for Business Card
Company Name - BrindlewayCare
Company locations: United Kingdom, Australia, New Zealand
Staff Details:
Staff name: Derek Mallow
Staff job title: Executive Chairman
Staff email: d.mallow@plumvora.example
Office phone number: 01742 918576
Font styles to use
Other font styles liked:
- Calibri
Requirements
Must have
- Must include the BrindlewayCare brand name in it's current font
- Must include logo (3 leaves in gold circle)
- Must include Business Card Details
Nice to have
- Elements of gold
- White space
- Something autumn themed but not too cliched
Should not have
- No blue - used by a major competitor and we would like to differentiate from them
- Large blocks of dark green colour (the green that appears in our leaves on the logo on our current business card is the background colour and it is far too dark)

```html
<!DOCTYPE html>
<html lang="en">
<head>
<meta charset="utf-8">
<title>BrindlewayCare Business Card</title>
<link href="https://fonts.googleapis.com/css2?family=Open+Sans:wght@400;700&display=swap" rel="stylesheet">
<style>
  :root {
    --backdrop: #2b2d31;
    --card: #ffffff;
    --gold: #a39468;
    --ink: #1c1c1c;
    --leaf-red: #a8283f;
    --leaf-olive: #a9a12a;
    --leaf-green: #5d8a2e;
  }
  * { margin: 0; padding: 0; box-sizing: border-box; }
  html, body {
    width: 1200px;
    height: 864px;
    overflow: hidden;
    background: var(--backdrop);
    font-family: "Open Sans", Calibri, sans-serif;
  }
  .canvas {
    position: relative;
    width: 1200px;
    height: 864px;
  }
  .card {
    position: absolute;
    width: 560px;
    height: 320px;
    background: var(--card);
    overflow: hidden;
  }
  .card--front { left: 320px; top: 72px; }
  .card--back  { left: 320px; top: 472px; }

  /* Front face */
  .front-brand {
    position: absolute;
    left: 0; right: 0; top: 0; bottom: 0;
    display: flex;
    align-items: center;
    justify-content: center;
    gap: 18px;
  }
  .brand-ring {
    width: 92px;
    height: 92px;
    border: 3px solid var(--gold);
    border-radius: 50%;
  }
  .brand-name {
    font-family: "Open Sans", Calibri, sans-serif;
    font-weight: 400;
    color: var(--gold);
    letter-spacing: 0.5px;
  }
  .front-brand .brand-name { font-size: 40px; }

  /* Back face */
  .back-details {
    position: absolute;
    left: 36px;
    top: 26px;
  }
  .back-details .brand-name {
    font-size: 42px;
    line-height: 1.1;
    display: block;
    margin-bottom: 14px;
  }
  .staff-name {
    font-size: 17px;
    font-weight: 700;
    color: var(--gold);
    margin-left: 20px;
  }
  .staff-title {
    font-size: 13px;
    color: var(--ink);
    margin-left: 20px;
  }
  .locations {
    font-size: 13px;
    color: var(--ink);
    margin-top: 22px;
    line-height: 1.3;
    margin-left: 6px;
  }
  .contact {
    display: flex;
    align-items: center;
    gap: 8px;
    font-size: 13px;
    color: var(--ink);
    margin-top: 26px;
  }
  .contact-icon { width: 12px; height: 12px; fill: var(--gold); }
  .leaf-art {
    position: absolute;
    right: 24px;
    top: 30px;
    width: 170px;
    height: 290px;
    background: linear-gradient(135deg, var(--leaf-green) 0%, var(--leaf-olive) 50%, var(--leaf-red) 100%);
    opacity: 0.85;
  }
</style>
</head>
<body>
  <main class="canvas">
    <section class="card card--front" aria-label="Business card front">
      <div class="front-brand">
        <span class="brand-ring" aria-hidden="true"></span>
        <span class="brand-name">BrindlewayCare</span>
      </div>
    </section>

    <section class="card card--back" aria-label="Business card back">
      <div class="back-details">
        <span class="brand-name">BrindlewayCare</span>
        <p class="staff-name">Derek Mallow</p>
        <p class="staff-title">Executive Chairman</p>
        <p class="locations">United Kingdom, Australia<br>New Zealand</p>
        <p class="contact">
          <svg class="contact-icon" viewBox="0 0 24 24" aria-hidden="true">
            <path d="M6.6 10.8c1.4 2.8 3.8 5.1 6.6 6.6l2.2-2.2c.3-.3.7-.4 1-.2 1.1.4 2.3.6 3.6.6.6 0 1 .4 1 1V20c0 .6-.4 1-1 1C10.6 21 3 13.4 3 4c0-.6.4-1 1-1h3.5c.6 0 1 .4 1 1 0 1.3.2 2.5.6 3.6.1.3 0 .7-.2 1L6.6 10.8z"/>
          </svg>
          d.mallow@plumvora.example
        </p>
      </div>
      <div class="leaf-art" role="img" aria-label="Decorative autumn leaves illustration in green, olive and red"></div>
    </section>
  </main>
</body>
</html>
```